I have a logo and need to design the business card and stationery.
Updates

The uploaded logo image named as GREYMARSH CONSTRUCTION which is to be replaced to GREYMARSH CONTRACTS. Kindly add below details and submit the designs- Company name- Greymarsh Engineering Contracts LLP Name & Post- Kelvan Joshi (Designated Partner) Address- Block No.317, Wing C, Tulvo Trade Court, Manek Pural Road, Ruparel Industrial Estate, Goregaon(E), Mumbai - 400 063 Contact- +91 97415 60382 Email- kelvanjoshi@mailbrook.example Website- www.greymarshcontracts.example Contact for Letterhead- +91-22-28754193

Hi Tovin Rahul, We are liking your Design #28860835. We have suggested some changes which are mentioned in feedback. Kindly revert with it asap to finalize this design.

Colors

Designer to choose colors to be used in the design.

```html
<!DOCTYPE html>
<html lang="en">
<head>
<meta charset="utf-8">
<title>Greymarsh Contracts – Business Card</title>
<link rel="stylesheet" href="https://fonts.googleapis.com/css2?family=Poppins:wght@400;500;600&family=Lato:wght@400&family=Syncopate:wght@700&display=swap">
<style>
  :root {
    --canvas: #b8b8b8;
    --paper: #ffffff;
    --ink: #2b2b2b;
    --rule: #5a5a5a;
    --card-dark: #151515;
    --card-dark-2: #2a2a2a;
    --mark-light: #e6e6e6;
  }
  * { margin: 0; padding: 0; box-sizing: border-box; }
  html, body { width: 1200px; height: 801px; overflow: hidden; background: var(--canvas); }
  .canvas { position: relative; width: 1200px; height: 801px; }

  .card { position: absolute; top: 274px; width: 443px; height: 263px; }
  .card-front { left: 153px; background: var(--paper); color: var(--ink); }
  .card-back { left: 625px; overflow: hidden; }

  .wordmark {
    position: absolute; right: 20px; top: 28px; text-align: right;
    font-family: "Syncopate", sans-serif; font-weight: 700; color: var(--ink);
    line-height: 1.15;
  }
  .wordmark span { display: block; }
  .wordmark .word-main { font-size: 19px; }
  .wordmark .word-sub { font-size: 15px; letter-spacing: 4px; margin-right: -4px; }

  .person { position: absolute; left: 20px; top: 92px; }
  .person-name { font-family: "Poppins", sans-serif; font-weight: 500; font-size: 16px; letter-spacing: 0.2px; }
  .person-role { font-family: "Lato", sans-serif; font-size: 12px; margin-top: -2px; }

  .contacts { position: absolute; right: 22px; top: 116px; list-style: none; }
  .contact {
    display: flex; align-items: center; justify-content: flex-end; gap: 6px;
    height: 21px; font-family: "Poppins", sans-serif; font-size: 12.5px;
  }
  .contact svg { width: 17px; height: 17px; flex: none; }

  .divider { position: absolute; left: 0; right: 22px; top: 185px; height: 1px; background: var(--rule); }

  .company { position: absolute; left: 0; right: 0; top: 195px; text-align: center; }
  .company-name { font-family: "Poppins", sans-serif; font-weight: 600; font-size: 13.5px; letter-spacing: 0.2px; }
  .company-address { font-family: "Lato", sans-serif; font-size: 11px; line-height: 15px; margin-top: 3px; }

  .back-pattern { position: absolute; inset: 0; background: radial-gradient(ellipse at 70% 55%, var(--card-dark-2), var(--card-dark) 75%); }
  .back-mark { position: absolute; left: 220px; top: 119px; text-align: center; color: var(--mark-light); }
  .back-square { width: 58px; height: 57px; border: 6px solid var(--mark-light); margin: 0 auto 9px; }
  .back-name { font-family: "Syncopate", sans-serif; font-weight: 700; line-height: 1.15; }
  .back-name span { display: block; }
  .back-name .word-main { font-size: 14px; }
  .back-name .word-sub { font-size: 11px; letter-spacing: 3px; }
</style>
</head>
<body>
<main class="canvas">
  <section class="card card-front">
    <div class="wordmark"><span class="word-main">GREYMARSH</span><span class="word-sub">CONTRACTS</span></div>

    <div class="person">
      <p class="person-name">KELVAN JOSHI</p>
      <p class="person-role">Designated Partner</p>
    </div>

    <ul class="contacts">
      <li class="contact">+91 97415 60382
        <svg viewBox="0 0 17 17" aria-hidden="true"><rect x="0.75" y="0.75" width="15.5" height="15.5" rx="2.5" fill="none" stroke="#2b2b2b" stroke-width="1.5"/><path d="M5 4.2l1.8-.4 1 2.3-1 .8c.5 1.2 1.3 2 2.4 2.5l.8-1 2.3 1-.4 1.8c-3.6-.2-6.6-3.2-6.9-7z" fill="#2b2b2b"/></svg>
      </li>
      <li class="contact">kelvanjoshi@mailbrook.example
        <svg viewBox="0 0 17 17" aria-hidden="true"><rect x="0.75" y="0.75" width="15.5" height="15.5" rx="2.5" fill="none" stroke="#2b2b2b" stroke-width="1.5"/><rect x="3.5" y="5" width="10" height="7" fill="none" stroke="#2b2b2b" stroke-width="1.1"/><path d="M3.5 5l5 4 5-4M3.5 12l3.5-3.5M13.5 12L10 8.5" fill="none" stroke="#2b2b2b" stroke-width="1"/></svg>
      </li>
      <li class="contact">www.greymarshcontracts.example
        <svg viewBox="0 0 17 17" aria-hidden="true"><rect x="0.75" y="0.75" width="15.5" height="15.5" rx="2.5" fill="none" stroke="#2b2b2b" stroke-width="1.5"/><circle cx="8.5" cy="8.5" r="4.8" fill="none" stroke="#2b2b2b" stroke-width="1"/><ellipse cx="8.5" cy="8.5" rx="2" ry="4.8" fill="none" stroke="#2b2b2b" stroke-width="0.9"/><path d="M3.7 8.5h9.6M4.4 6h8.2M4.4 11h8.2" stroke="#2b2b2b" stroke-width="0.9"/></svg>
      </li>
    </ul>

    <div class="divider"></div>

    <div class="company">
      <p class="company-name">GREYMARSH ENGINEERING CONTRACTS LLP</p>
      <p class="company-address">Block No.317, Wing C, Tulvo Trade Court, Manek Pural Road,<br>Ruparel Industrial Estate, Goregaon(E), Mumbai - 400 063</p>
    </div>
  </section>

  <section class="card card-back">
    <div class="back-pattern" role="img" aria-label="Dark repeating geometric pattern background"></div>
    <div class="back-mark">
      <div class="back-square"></div>
      <p class="back-name"><span class="word-main">GREYMARSH</span><span class="word-sub">CONTRACTS</span></p>
    </div>
  </section>
</main>
</body>
</html>
```